Lotstallmart.com Webpage Design

Design Brief for lotstallmart.com (Copy of Brief also in attached Word file)

Name of Website- lotstallmart.com (existing logo and look & feel of website to be changed)

Logo - Finalised. The logo files are attached with the brief as “logo.jpeg”. The “Blue- Grey” version of the logo is for use on lighter backgrounds and the “Orange-White” version of the logo is for use on darker backgrounds. (A full Black version of the logo is also attached). Both versions may be used in different parts of the website. All attached files are in .png format.
Status - The website in functional and is undergoing user trials. However, we want to improve the look & feel of the website so at it seems
a. cotemporary,
b. Easy to Navigate
c. professional and
d. Vibrant.

Please visit ‘lotstallmart.com’ to check out the website and its functionalities – please use it only as a reference for the features & functions to be provided, however the designer should use a ‘Free Hand’ in designing the composition of various parts of the webpage without getting too influenced by the existing design

Objective of the Website ‘lotstallmart.com –
a. It is a portal focussed on listing of ‘Retail’ specific real-estate properties by developers, owners and realty brokers. The properties shall listed under the following four categories-
i. Retail Malls
ii. Shopping Complexes
iii. High-street shops
iv. Retail Warehouses
*refer lotstallmart.com for better clarity

b. The abovementioned properties shall be listed either for ‘Sale’ or ‘rent\lease’ or both

c. Users shall visit the site in case they wish to acquire a retail \ shop space either on ‘sale’ or ‘rent’. These Users would be able to specify the ‘Search Criteria’ through the tool-bars provided on the website – the ‘Search Criteria’ shall comprise of ‘Type of space category’, ‘City’, ‘Locality’, transaction type ie ‘Rent \ Sale’ and ‘Area Range’

d. The main revenue model for the website shall be listing fee ( or advertising charges ) payable by those listing their properties on the website.

Three Main Pages of Website (lotstallmart.com) that need to be designed -
a. Main Home Page (visit the web link - http://lotstallmart.com/ ) - The main home page has the “Search Toolbar” for specifying of Search Criteria by the User. It shall also have the following features & functions-
i. Main Advertising Banner
ii. Featured Projects
iii. New Launches
iv. Toolbar with buttons – ‘Advertise with Us’, ‘Listings Alert’, ‘Mart Wizards’, ‘Advertiser Login’

b. Property Listings Page (visit the web link - http://lotstallmart.com/gurgaon-in-india ) - The List of property options that match the Criteria specified by the ‘User’ get displayed on this page.

c. Property Detail Page - When the ‘User’ clicks on the “More….” Button on the ‘Property Listings Page’ (given in point b. above) the web page with the details of the property opens. (For Example – visit the web link - http://lotstallmart.com/vorne-Shopping-Complex-vorne-quadrion-gurgaon-636 )

Note:- Please refer to attached ‘Shopping’ related images the designer may use them on the website to provide a look & feel of retail if required – either separately or rotate in a single window

Target Market(s)

Retailers & Investors looking for retail space, Real Estate Brokers, Developers

Industry/Entity Type

Advertising

Number of Pages Required

3 page

Requirements
Must have
• Refer to existing site lotstallmart.com -- all the existing functionalities are a must have.
Nice to have
• The Designer may use the retail related images on the website if required for making it more vibrant. Refer attached images Shopping(1-6).jpg

```html
<!DOCTYPE html>
<html lang="en">
<head>
<meta charset="utf-8">
<title>Lotstallmart.com – Find Perfect Place for Your Retail Store</title>
<link href="https://fonts.googleapis.com/css2?family=Open+Sans:wght@400;600;700;800&display=swap" rel="stylesheet">
<style>
:root{
  --orange:#f4a41f;
  --orange-dark:#e08e0b;
  --blue:#1d8fe6;
  --ink:#2b2b2b;
  --text:#555;
  --muted:#888;
  --line:#dcdcdc;
  --band:#eeeeee;
  --white:#fff;
  --topbar:#1f2a36;
}
*{box-sizing:border-box;margin:0;padding:0}
html,body{width:1200px;height:3030px;overflow:hidden}
body{font-family:"Open Sans",Arial,sans-serif;color:var(--text);background:var(--white);font-size:13px}
.wrap{width:830px;margin:0 auto;position:relative}

.city-bar{height:15px;background:var(--topbar);color:#cfd6de;font-size:9px;line-height:15px}
.city-bar .wrap{text-align:right}
.city-bar span{padding:0 3px}

.site-header{height:85px;border-bottom:1px solid var(--line)}
.site-header .wrap{height:85px;display:flex;align-items:center;justify-content:space-between}
.brand{display:flex;align-items:center;gap:10px}
.brand-dot{width:26px;height:26px;border-radius:50%;background:var(--blue)}
.brand-name{font-size:26px;font-weight:700;color:var(--blue);letter-spacing:-.5px}
.main-nav{display:flex;align-items:center;gap:26px}
.main-nav a{color:var(--ink);text-decoration:none;font-size:13px;font-weight:600;text-align:center;line-height:1.2}
.main-nav a small{display:block;font-size:9px;font-weight:400;color:var(--muted)}
.main-nav a.active{color:var(--blue)}
.login-box{text-align:center;font-size:9px;color:var(--muted)}
.login-btn{display:block;background:var(--blue);color:#fff;font-weight:700;font-size:12px;padding:6px 14px;border-radius:3px;margin:3px 0}

.hero{height:528px;position:relative;background:linear-gradient(100deg,#3a2a22 0%,#6b4a33 35%,#8d6a4a 55%,#3f3a3e 100%)}
.hero-photo{position:absolute;inset:0;background:radial-gradient(ellipse at 30% 30%,rgba(240,200,150,.35),transparent 60%),radial-gradient(ellipse at 70% 80%,rgba(20,25,40,.5),transparent 60%)}
.hero-title{position:absolute;left:185px;top:318px;color:#fff;font-size:34px;font-weight:800;line-height:1.15;text-shadow:0 2px 4px rgba(0,0,0,.4)}
.search-panel{position:absolute;left:742px;top:21px;width:298px;height:486px;background:#fff;padding:16px 20px;box-shadow:0 2px 8px rgba(0,0,0,.3)}
.search-panel h2{font-size:20px;font-weight:700;color:var(--ink);margin-bottom:12px}
.search-panel h2 em{font-style:normal;color:var(--orange)}
.search-panel label{display:block;font-size:11px;color:var(--ink);margin:10px 0 5px}
.search-panel label u{color:var(--blue)}
.radio-grid{display:grid;grid-template-columns:1fr 1fr;gap:6px 8px;font-size:11px}
.radio-grid span{display:flex;align-items:center;gap:5px}
.radio-grid i{width:11px;height:11px;border:1px solid #999;border-radius:50%;display:inline-block}
.field{height:28px;border:1px solid var(--line);font-size:11px;color:var(--muted);padding:0 10px;display:flex;align-items:center;justify-content:space-between}
.field svg{width:8px;height:6px}
.search-btn{margin-top:18px;height:40px;background:var(--blue);color:#fff;font-weight:700;font-size:14px;display:flex;align-items:center;justify-content:center;border-radius:3px}

.categories{height:117px}
.categories .wrap{display:flex;justify-content:space-between;padding-top:22px}
.cat-tile{width:190px;height:77px;background:var(--orange);color:#3a2400;text-align:center;padding-top:18px;border-bottom:3px solid var(--orange-dark)}
.cat-tile b{display:block;font-size:15px;color:#2a1a00}
.cat-tile small{font-size:10px}

.section-head{display:flex;align-items:center;gap:10px;border-bottom:1px solid var(--line);padding-bottom:6px;margin-bottom:14px}
.section-head h2{font-size:20px;font-weight:700;color:var(--ink)}
.section-head h2 em{font-style:normal;color:var(--orange)}
.view-all{background:var(--ink);color:#fff;font-size:8px;font-weight:700;padding:2px 6px;border-radius:2px}

.listing{padding-top:18px}
.featured{height:667px}
.launches{height:628px;padding-top:40px}
.card-grid{display:grid;grid-template-columns:repeat(4,192px);justify-content:space-between;row-gap:40px}
.card{height:242px;display:flex;flex-direction:column}
.card-photo{height:138px;position:relative;flex:none}
.badge{position:absolute;right:4px;top:4px;background:rgba(30,30,30,.85);color:#fff;font-size:9px;font-weight:600;padding:2px 6px}
.card h3{font-size:16px;font-weight:700;color:var(--ink);margin-top:8px;line-height:1.3}
.card p{font-size:11px;line-height:1.35;color:var(--text);max-height:30px;overflow:hidden}
.view-btn{margin-top:auto;align-self:flex-start;background:var(--blue);color:#fff;font-size:10px;font-weight:700;padding:7px 14px;border-radius:2px}
.launches .card-grid{row-gap:30px}

.p1{background:linear-gradient(#b9d4ec,#8ea9c4 60%,#c8b7a0)}
.p2{background:linear-gradient(#2b3e58,#4d6481 55%,#a98f6b)}
.p3{background:linear-gradient(#cfe3f3,#9ab8d3 55%,#7c8b9b)}
.p4{background:linear-gradient(#9fc4e8,#5d82ad 60%,#3c5474)}
.p5{background:linear-gradient(#d8e3ec,#a9b8c6 55%,#777f88)}
.p6{background:linear-gradient(#c3ccd4,#8f9aa5 60%,#5b636c)}
.p7{background:linear-gradient(#d6c8b3,#a8917a 60%,#6a5a4a)}
.p8{background:linear-gradient(#b2cde6,#6f8fb1 55%,#d2b88a)}

.wizards{height:382px;background:var(--band);position:relative}
.wizards-photo{position:absolute;right:0;top:0;width:560px;height:360px;background:linear-gradient(90deg,var(--band) 0%,rgba(238,238,238,0) 30%),linear-gradient(135deg,#e8c99b,#d3a05a 45%,#9b6a3c 75%,#c7b49a)}
.wizards-form{position:absolute;left:185px;top:28px;width:480px}
.wizards-form h2{font-size:20px;font-weight:700;color:var(--ink);border-bottom:1px solid var(--line);padding-bottom:6px;width:475px}
.wizards-form h2 em{font-style:normal;color:var(--orange)}
.wizards-form p{font-size:12px;line-height:1.55;margin:12px 0;width:460px}
.input{height:32px;background:#fff;border:1px solid var(--line);font-size:11px;color:var(--muted);padding:0 10px;display:flex;align-items:center}
.row{display:flex;gap:8px}
.row .input{flex:1}
.textarea{height:60px;align-items:flex-start;padding-top:8px;margin-top:8px;width:475px}
.send-btn{width:180px;height:40px;background:var(--blue);color:#fff;font-weight:700;font-size:14px;display:flex;align-items:center;justify-content:center;border-radius:3px;margin-top:22px}

.about{height:358px;background:var(--band);padding-top:22px}
.about .wrap{display:flex;justify-content:space-between}
.about-text{width:390px}
.about-text h2,.alert-box h2{font-size:20px;font-weight:700;color:var(--ink);border-bottom:1px solid var(--line);padding-bottom:6px;margin-bottom:10px}
.about-text h2 em,.alert-box h2 em{font-style:normal;color:var(--orange)}
.about-text p{font-size:11.5px;line-height:1.55;margin-bottom:8px}
.about-text a{color:var(--blue);text-decoration:none}
.alert-box{width:424px;background:#fff;padding:14px 18px;height:320px}
.alert-box p{font-size:11px;margin-bottom:10px;line-height:1.4}
.alert-box .input{margin-bottom:4px;justify-content:space-between}
.alert-box .hint{font-size:8px;color:var(--muted);margin-bottom:8px}
.subscribe-btn{width:170px;height:40px;background:var(--blue);color:#fff;font-weight:700;font-size:13px;display:flex;align-items:center;justify-content:center;border-radius:3px;margin-top:6px}

.site-footer{height:300px;padding-top:22px}
.site-footer .wrap{display:grid;grid-template-columns:210px 230px 200px 1fr}
.site-footer h4{font-size:13px;font-weight:700;color:var(--ink);margin-bottom:12px}
.site-footer p,.site-footer li{font-size:11px;line-height:1.5;list-style:none}
.site-footer a{color:var(--blue);text-decoration:none}
.socials{display:flex;gap:8px}
.socials i{width:24px;height:24px;border-radius:50%;background:var(--orange);display:block}
.copyright{position:absolute;right:0;top:236px;font-size:10px;color:var(--muted)}
</style>
</head>
<body>

<div class="city-bar"><div class="wrap">
  <span>Bangalore</span>|<span>Chennai</span>|<span>Greater Noida</span>|<span>Gurgaon</span>|<span>Hyderabad</span>|<span>Jaipur</span>|<span>Kolkata</span>|<span>Mumbai</span>|<span>Noida</span>|<span>Pune</span>|<span>Surat</span>
</div></div>

<header class="site-header"><div class="wrap">
  <div class="brand"><span class="brand-dot"></span><span class="brand-name">lotstallmart</span></div>
  <nav class="main-nav">
    <a class="active" href="#">Home</a>
    <a href="#">Advertise with us<small>Standard listing - FREE</small></a>
    <a href="#">Mart Wizards<small>Shop search services</small></a>
    <a href="#">Listing Alert</a>
    <div class="login-box">List Your Property Here<span class="login-btn">Advertiser Login</span>New Advertiser : Register</div>
  </nav>
</div></header>

<section class="hero">
  <div class="hero-photo" role="img" aria-label="Family carrying shopping bags walking through a lit shopping arcade"></div>
  <h1 class="hero-title">Find Perfect Place for<br>Your Retail Store</h1>
  <form class="search-panel">
    <h2>Find your <em>stallspace</em></h2>
    <label>Select <u>Retail Format</u>:</label>
    <div class="radio-grid">
      <span><i></i>Retail Malls</span><span><i></i>Shopping Complex</span>
      <span><i></i>High Street Shops</span><span><i></i>Retail Warehouses</span>
    </div>
    <label>Sale Or Rent Or Both</label>
    <div class="field">Both<svg viewBox="0 0 8 6"><path d="M0 0h8L4 6z" fill="#777"/></svg></div>
    <label>Select City:</label>
    <div class="field">Select<svg viewBox="0 0 8 6"><path d="M0 0h8L4 6z" fill="#777"/></svg></div>
    <label>Select Locality/Micro Market</label>
    <div class="field">Select<svg viewBox="0 0 8 6"><path d="M0 0h8L4 6z" fill="#777"/></svg></div>
    <label>Enter Keywords:</label>
    <div class="field">Name of the Project, Developer etc</div>
    <div class="search-btn">SEARCH</div>
  </form>
</section>

<section class="categories"><div class="wrap">
  <div class="cat-tile"><b>Retail Malls</b><small>Centrally Air Conditioned</small></div>
  <div class="cat-tile"><b>Shopping Complex</b><small>Non Air Conditioned Building</small></div>
  <div class="cat-tile"><b>High Street Shops</b><small>Road Facing Retail</small></div>
  <div class="cat-tile"><b>Retail Warehouses</b><small>Back-end Retail Storage</small></div>
</div></section>

<section class="listing featured"><div class="wrap">
  <div class="section-head"><h2>Featured <em>Projects</em></h2><span class="view-all">VIEW ALL</span></div>
  <div class="card-grid">
    <article class="card"><div class="card-photo p1" role="img" aria-label="Retail mall exterior"><span class="badge">Retail Malls</span></div><h3>Surat</h3><p>Maple Arcade, Althan</p><span class="view-btn">VIEW THE LISTING</span></article>
    <article class="card"><div class="card-photo p2" role="img" aria-label="High street retail building at dusk"></div><h3>Faridabad</h3><p>Parkline High Street, Sector 81</p><span class="view-btn">VIEW THE LISTING</span></article>
    <article class="card"><div class="card-photo p3" role="img" aria-label="Shopping complex tower"><span class="badge">Shopping Complex</span></div><h3>Gurgaon</h3><p>Corvex Cosmopolis, Sector 65</p><span class="view-btn">VIEW THE LISTING</span></article>
    <article class="card"><div class="card-photo p4" role="img" aria-label="Tall retail mall tower"><span class="badge">Retail Malls</span></div><h3>Gurgaon</h3><p>Orbit 24K , Sohna Road</p><span class="view-btn">VIEW THE LISTING</span></article>
    <article class="card"><div class="card-photo p5" role="img" aria-label="Mall facade with forecourt"><span class="badge">Retail Malls</span></div><h3>New Delhi</h3><p>Harbor Mall, Tagore Garden,<br>Tagore Garden</p><span class="view-btn">VIEW THE LISTING</span></article>
    <article class="card"><div class="card-photo p6" role="img" aria-label="Mall interior atrium"><span class="badge">Retail Malls</span></div><h3>Chennai</h3><p>Elmora Skywalk Mall , Aminjikarai</p><span class="view-btn">VIEW THE LISTING</span></article>
    <article class="card"><div class="card-photo p7" role="img" aria-label="Mall interior with shopfronts"><span class="badge">Retail Malls</span></div><h3>Chennai</h3><p>The Royal Mall , Velachery</p><span class="view-btn">VIEW THE LISTING</span></article>
    <article class="card"><div class="card-photo p8" role="img" aria-label="Shopping complex with glass frontage"><span class="badge">Shopping Complex</span></div><h3>Gurgaon</h3><p>Orlen Galleria 55 ,<br>Golf Course Road</p><span class="view-btn">VIEW THE LISTING</span></article>
  </div>
</div></section>

<section class="wizards">
  <div class="wizards-photo" role="img" aria-label="Family with shopping bags in front of a sale sign"></div>
  <form class="wizards-form">
    <h2>Mart <em>Wizards</em></h2>
    <p>Post your Retail Space requirement with us and our experts shall get back with suitable options and even help you in your transaction. This is a <b>Free Service!</b></p>
    <div class="row"><div class="input">Enter your email address</div><div class="input">Mobile</div></div>
    <div class="input textarea">Add Description of Requirement</div>
    <div class="send-btn">SEND</div>
  </form>
</section>

<section class="listing launches"><div class="wrap">
  <div class="section-head"><h2>New <em>Launches</em></h2><span class="view-all">VIEW ALL</span></div>
  <div class="card-grid">
    <article class="card"><div class="card-photo p5" role="img" aria-label="Retail mall under blue sky"><span class="badge">Retail Malls</span></div><h3>Bhopal</h3><p>The Grand Indus Place,<br>Hill Road</p><span class="view-btn">VIEW THE LISTING</span></article>
    <article class="card"><div class="card-photo p2" role="img" aria-label="Mall building at night"></div><h3>Noida</h3><p>Crest One , Sector 18</p><span class="view-btn">VIEW THE LISTING</span></article>
    <article class="card"><div class="card-photo p3" role="img" aria-label="Shopping complex building"><span class="badge">Shopping Complex</span></div><h3>Mohali</h3><p>City Core - SCO Sector ,<br>Sihan Majra</p><span class="view-btn">VIEW THE LISTING</span></article>
    <article class="card"><div class="card-photo p1" role="img" aria-label="Row of shop offices"><span class="badge">Shopping Complex</span></div><h3>Mohali</h3><p>SCO in Sector 123 On ,<br>Sihan Majra</p><span class="view-btn">VIEW THE LISTING</span></article>
    <article class="card"><div class="card-photo p6" role="img" aria-label="Shopping complex frontage"><span class="badge">Shopping Complex</span></div><h3>Gurgaon</h3><p>The Azurite Sector 49 ,<br>Sector 102</p><span class="view-btn">VIEW THE LISTING</span></article>
    <article class="card"><div class="card-photo p4" role="img" aria-label="Mall tower"><span class="badge">Retail Malls</span></div><h3>New Delhi</h3><p>Pranav Mall , Rohini</p><span class="view-btn">VIEW THE LISTING</span></article>
    <article class="card"><div class="card-photo p8" role="img" aria-label="Glass-fronted shopping complex"><span class="badge">Shopping Complex</span></div><h3>Gurgaon</h3><p>Velora Trinity, Dwarka<br>Expressway</p><span class="view-btn">VIEW THE LISTING</span></article>
    <article class="card"><div class="card-photo p7" role="img" aria-label="Large mall exterior"><span class="badge">Retail Malls</span></div><h3>Thiruvananthapuram</h3><p>Bay Mall , NH Bypass</p><span class="view-btn">VIEW THE LISTING</span></article>
  </div>
</div></section>

<section class="about"><div class="wrap">
  <div class="about-text">
    <h2>About <em>Us</em></h2>
    <p>Lotstallmart.com is a Specialized Web based platform for Retail Space, featuring properties across India under various formats such as Retail Malls, Shopping Complexes, High-street Shops. Also featured are Retail Warehouses which provide the logistic back end for the retail business. Lotstallmart.com is useful to various category of users as follows:</p>
    <p><b>a. Developers</b>- For advertising their retail developments on a focussed platform that gets accessed by Retailers, Investors and the Broking community.... <a href="#">read more</a></p>
  </div>
  <form class="alert-box">
    <h2>Listing <em>Alert</em></h2>
    <p>Subscribe for Fortnightly Email update on New Listings @ Lotstallmart</p>
    <div class="input">Enter your email address</div>
    <div class="hint"></div>
    <div class="input">Select Option <svg width="8" height="6" viewBox="0 0 8 6"><path d="M0 0h8L4 6z" fill="#777"/></svg></div>
    <div class="hint">(select state format of interest)</div>
    <div class="input">Allahabad <svg width="8" height="6" viewBox="0 0 8 6"><path d="M0 0h8L4 6z" fill="#777"/></svg></div>
    <div class="hint">(select city of interest)</div>
    <div class="subscribe-btn">SUBSCRIBE</div>
  </form>
</div></section>

<footer class="site-footer"><div class="wrap">
  <div><h4>Contact</h4><p>Stall Point<br>Unit 12, 2nd Floor,<br>Harbour Lane, Block c,<br>Sector b, Pinecity - 100001<br><br>Phone : 000-000-0000<br>Fax : 000-000-0000</p></div>
  <div><h4>Editor's Choice</h4><p>A "Select" Listing of Retail Properties Handpicked by our Editors based on their own positive evaluation on parameters &amp; attributes such as Design Concept, Location, Developer... <a href="#">read more</a></p></div>
  <div><h4>Privacy</h4><ul><li>Privacy Policy</li><li>Terms of Use</li><li>About Us</li><li>Contact Us</li><li>Sitemap</li></ul></div>
  <div><h4>Follow Us</h4><div class="socials"><i></i><i></i><i></i><i></i></div></div>
  <div class="copyright">All rights reserved © 2015 Lotstallmart.com</div>
</div></footer>

</body>
</html>
```